The quiet harbor with an elephant incorporated in the background

Target Market(s)

Real estate

Industry/Entity Type

Real Estate

Contact Information for Business Card

On back on want my name & number
In front I want the business name, "the quiet harbor", below to say staging & design

Logo Text

The quiet harbor

Font styles to use
Serif

Colors
000000

Requirements
Must have
• I want an elephant behind the writing in gold transperant

```html
<!DOCTYPE html>
<html lang="en">
<head>
<meta charset="utf-8">
<title>The Quiet Harbor – Business Card</title>
<link href="https://fonts.googleapis.com/css2?family=Questrial&family=Open+Sans:wght@400;700&display=swap" rel="stylesheet">
<style>
  :root {
    --backdrop: #6a6a6a;
    --card-dark: #282322;
    --card-gold: #dfb21b;
    --gold: #e3b01c;
    --ink-light: #ececec;
    --white: #ffffff;
  }
  html, body {
    margin: 0;
    width: 1200px;
    height: 900px;
    overflow: hidden;
  }
  body {
    position: relative;
    background: radial-gradient(ellipse at 50% 45%, #727272 0%, var(--backdrop) 70%, #626262 100%);
    font-family: "Open Sans", Arial, sans-serif;
  }
  .card {
    position: absolute;
    top: 170px;
    width: 347px;
    height: 560px;
    overflow: hidden;
    box-shadow: 0 2px 6px rgba(0,0,0,0.25);
  }
  .card--back { left: 259px; background: var(--card-dark); }
  .card--front { left: 631px; background: var(--card-gold); }

  .elephant-backdrop {
    position: absolute;
    left: 8px;
    top: 240px;
    width: 330px;
    height: 320px;
    border-radius: 48% 52% 0 0 / 40% 40% 0 0;
    background: linear-gradient(180deg, rgba(255,255,255,0.035), rgba(255,255,255,0.02));
  }

  .brand-mark {
    position: absolute;
    left: 50%;
    border-radius: 50%;
    transform: translateX(-50%);
  }
  .card--back .brand-mark { top: 73px; width: 92px; height: 92px; background: var(--gold); }
  .card--front .brand-mark { top: 188px; width: 96px; height: 96px; background: var(--white); }

  .brand-name,
  .brand-tagline {
    position: absolute;
    left: 0;
    right: 0;
    margin: 0;
    text-align: center;
    font-family: "Questrial", "Century Gothic", sans-serif;
    font-weight: 400;
    white-space: nowrap;
  }
  .brand-name { font-size: 28px; letter-spacing: 0.5px; }
  .brand-tagline { font-size: 14px; letter-spacing: 0.6px; }
  .card--back .brand-name { top: 205px; color: var(--gold); }
  .card--back .brand-tagline { top: 245px; color: #9b8a5a; }
  .card--front .brand-name { top: 330px; color: var(--white); }
  .card--front .brand-tagline { top: 368px; color: var(--white); }

  .person-name {
    position: absolute;
    top: 378px;
    left: 0;
    right: 0;
    margin: 0;
    text-align: center;
    color: var(--gold);
    font-weight: 700;
    font-size: 21px;
    letter-spacing: 0.3px;
  }
  .divider {
    position: absolute;
    top: 432px;
    left: 100px;
    width: 147px;
    height: 1px;
    background: var(--gold);
  }
  .contact {
    position: absolute;
    top: 465px;
    left: 0;
    right: 0;
    margin: 0;
    padding: 0;
    list-style: none;
    text-align: center;
    color: var(--ink-light);
    font-size: 16.5px;
    line-height: 26px;
  }
  .contact svg {
    width: 17px;
    height: 15px;
    vertical-align: -2px;
    margin-right: 5px;
    fill: var(--gold);
  }
</style>
</head>
<body>
  <section class="card card--back">
    <div class="elephant-backdrop" role="img" aria-label="Faint gold elephant silhouette behind the lettering"></div>
    <div class="brand-mark"></div>
    <p class="brand-name">THE QUIET HARBOR</p>
    <p class="brand-tagline">STAGING &amp; DESIGN</p>
    <p class="person-name">DANIEL REEVES</p>
    <div class="divider"></div>
    <ul class="contact">
      <li><svg viewBox="0 0 24 24"><path d="M6.6 10.8a15.2 15.2 0 0 0 6.6 6.6l2.2-2.2a1 1 0 0 1 1-.25 11.4 11.4 0 0 0 3.6.57 1 1 0 0 1 1 1V20a1 1 0 0 1-1 1A17 17 0 0 1 3 4a1 1 0 0 1 1-1h3.5a1 1 0 0 1 1 1c0 1.25.2 2.45.57 3.57a1 1 0 0 1-.25 1z"/></svg>(044)987654321</li>
      <li><svg viewBox="0 0 24 18"><path d="M0 0h24v18H0z M1.5 1.5 12 10 22.5 1.5" fill="var(--gold)"/><path d="M1.5 1.5 12 10 22.5 1.5" fill="none" stroke="#282322" stroke-width="1.4"/></svg>hello@quietharbor.com</li>
    </ul>
  </section>

  <section class="card card--front">
    <div class="brand-mark"></div>
    <p class="brand-name">THE QUIET HARBOR</p>
    <p class="brand-tagline">STAGING &amp; DESIGN</p>
  </section>
</body>
</html>
```